ORV Fashion Design Company Needs a New Web Design, Please Click Me

Designers:

PLEASE NOTE: we only need the web page design, not a fully coded website.

Our brand's name is Orbel Vantra, our signature is print. our style is edgy and chic.

The old website is too messy. here's the address:
www.orvdesign.example.cn

The new website's purpose is to show our brand/design and most importantly, sell products, So it should be a combination of a designer official website and online shopping. I want the whole style to be clean, edgy and pioneer, easy to understand. we need a sophisticated online shopping website.

The reference websites are:
liromapek.example.uk
www.qd-besu.example
talemkorv.example
misolvare.example
pardelunitram.example

Please beat their designs :)

Check out our lasted fashion show to get to know us more.

https://www.videohost.example/watch?v=ZkrpLmWnaYd&spfreload=10

The attachments are our Logo and some 2015 Look Book.
(Please let us know if you want to play with our print in this particular web design, we can send the source file.)
Updates

Designers, we really like the design of helenamardoux.example(we have attached a picture of the website) , Can we get a homepage like that? so the designs you submit will be 3 pages. The first one should be a page that only has Shop/Look. then the shop page, it should be nothing but our product which we will list the categories ourself. And the look page should contain all the info. such as news, about us and designers etc. Thank you all for your hard work, we really enjoyed the designs. Added Monday, November 03, 2014

Target Market(s)

Our target audiences are woman aged from 16-40 who like online shopping

Industry/Entity Type

Online Shopping

Number of Pages Required

3 page

Font styles to use
Serif
Sans Serif
Script

Requirements
Must have
• Designers,
• we really like the design of helenamardoux.example(we have attached a picture of the website) , Can we get a homepage like that? so the designs you submit will be 3 pages. The first one should be a page that only has Shop/Look. then the shop page, it should be nothing but our product which we will list the categories ourself. And the look page should contain all the info. such as news, about us and designers etc. Thank you all for your hard work, we really enjoyed the designs.

```html
<!DOCTYPE html>
<html lang="en">
<head>
<meta charset="utf-8">
<title>Orbel Vantra — Home</title>
<link href="https://fonts.googleapis.com/css2?family=Lato:wght@300;400;700;900&family=Cinzel:wght@400&display=swap" rel="stylesheet">
<style>
  :root {
    --red: #b30000;
    --red-text: #c8102e;
    --black: #000;
    --white: #fff;
    --panel: #ebebeb;
    --ink: #222;
    --footer: #ececec;
    --icon-grey: #4a4a4a;
  }
  * { box-sizing: border-box; margin: 0; padding: 0; }
  html, body { width: 806px; height: 1200px; overflow: hidden; background: var(--white); font-family: "Lato", sans-serif; color: var(--ink); }
  .page { position: relative; width: 806px; height: 1200px; }

  .sidebar { position: absolute; left: 0; top: 0; width: 271px; height: 457px; background: var(--panel); }
  .brand { position: absolute; top: 22px; left: 0; width: 271px; text-align: center; }
  .brand-mark { display: block; width: 40px; height: 40px; margin: 0 auto 6px; border-radius: 50%; background: var(--red); }
  .brand-name { font-family: "Cinzel", serif; font-size: 10px; line-height: 11px; letter-spacing: 1px; color: var(--ink); }
  .main-nav { position: absolute; top: 140px; left: 0; width: 271px; list-style: none; text-align: center; }
  .main-nav li { height: 39px; font-size: 12.5px; letter-spacing: .3px; color: var(--ink); }

  .hero { position: absolute; left: 271px; top: 0; width: 535px; height: 457px; background: var(--black); overflow: hidden; }
  .hero-art {
    position: absolute; left: 0; top: 0; width: 190px; height: 457px;
    background:
      radial-gradient(ellipse 60px 90px at 20px 110px, rgba(235,235,235,.75), transparent 70%),
      radial-gradient(ellipse 50px 70px at 30px 300px, rgba(220,220,220,.6), transparent 70%),
      radial-gradient(ellipse 70px 60px at 130px 60px, rgba(200,200,200,.5), transparent 70%),
      radial-gradient(ellipse 90px 80px at 150px 420px, rgba(190,190,190,.45), transparent 70%),
      radial-gradient(ellipse 60px 120px at 90px 220px, rgba(120,120,120,.5), transparent 70%),
      linear-gradient(180deg, #2a2a2a 0%, #141414 50%, #2c2c2c 100%);
  }
  .account-links { position: absolute; right: 72px; top: 27px; font-size: 9px; color: var(--white); }
  .account-links .login { color: var(--red-text); }
  .hero-title { position: absolute; left: 315px; top: 241px; font-family: "Cinzel", serif; font-size: 9px; letter-spacing: 1.2px; color: var(--white); }
  .hero-thumb { position: absolute; top: 336px; width: 121px; height: 83px; border: 3px solid #ddd; }
  .thumb-1 {
    left: 28px;
    background:
      linear-gradient(90deg, transparent 50%, rgba(0,0,0,0) 50%),
      radial-gradient(circle at 25% 50%, #e9c46a 0, #b87a3a 25%, #7a8bb8 55%, transparent 75%),
      linear-gradient(90deg, #c9954a 0, #8e7fb0 48%, #1d2b52 50%, #3b5f9a 75%, #1a2748 100%);
  }
  .thumb-2 {
    left: 176px;
    background:
      radial-gradient(circle at 72% 50%, #bfe0f7 0, #4c8fcf 30%, transparent 60%),
      linear-gradient(90deg, #0f1d3a 0, #2d5fa0 25%, #142a55 48%, #1e4a86 52%, #0d1c3c 100%);
  }
  .thumb-3 {
    left: 323px;
    background:
      radial-gradient(circle at 78% 45%, #8fb8ee 0, #3d6ec4 35%, transparent 65%),
      linear-gradient(90deg, #223f78 0, #3b66b8 30%, #1d3668 48%, #2a55a6 52%, #5f8ad0 100%);
  }
  .slider-dots { position: absolute; left: 226px; top: 437px; display: flex; gap: 3px; }
  .slider-dots span { width: 6px; height: 6px; border-radius: 50%; background: #aaa; }
  .slider-dots .active { background: var(--red-text); }

  .side-tools { position: absolute; right: 0; top: 46px; width: 33px; }
  .side-tools span { display: block; width: 33px; height: 26px; margin-bottom: 6px; background: var(--icon-grey); }
  .side-tools .active { background: var(--red); }
  .side-tools svg { display: block; margin: 5px auto; }

  .video-label { position: absolute; left: 0; top: 454px; width: 271px; height: 288px; background: var(--red); }
  .video-label h2 { position: absolute; left: 72px; top: 127px; font-size: 21px; font-weight: 400; color: var(--white); }
  .video-frame {
    position: absolute; left: 271px; top: 457px; width: 535px; height: 285px;
    background:
      radial-gradient(ellipse 130px 110px at 430px 110px, rgba(30,30,30,.55), transparent 75%),
      radial-gradient(ellipse 160px 40px at 250px 210px, rgba(70,70,70,.7), transparent 75%),
      linear-gradient(180deg, #e6e6e6 0%, #d3d3d3 55%, #7d7d7d 70%, #a9a9a9 80%, #c8c8c8 100%);
  }
  .play-button { position: absolute; left: 220px; top: 114px; }

  .featured { position: absolute; left: 0; top: 770px; width: 806px; }
  .featured h3 { text-align: center; font-size: 12px; font-weight: 700; letter-spacing: .3px; color: var(--ink); }
  .product { position: absolute; top: 32px; width: 150px; }
  .product-photo { width: 148px; height: 225px; }
  .photo-blue {
    background:
      radial-gradient(ellipse 22px 95px at 74px 125px, #1f4f9c, #2d63b4 55%, transparent 75%),
      repeating-linear-gradient(90deg, rgba(255,255,255,.18) 0 3px, transparent 3px 11px),
      linear-gradient(180deg, #7cc4ea, #4fa7dc 55%, #9ed2ee 85%, #d6ecf7);
  }
  .photo-grey {
    background:
      radial-gradient(ellipse 24px 90px at 74px 115px, #4c4c4c, #6a6a6a 55%, transparent 75%),
      repeating-linear-gradient(90deg, rgba(255,255,255,.14) 0 3px, transparent 3px 10px),
      linear-gradient(180deg, #8c8c8c, #b8b8b8 55%, #a2a2a2 85%, #c6c6c6);
  }
  .product-name { margin-top: 18px; font-size: 12px; font-weight: 300; color: var(--ink); }
  .product-price { margin-top: 1px; font-size: 16px; font-weight: 300; color: var(--red-text); }
  .product-designer { margin-top: 3px; font-size: 8px; font-weight: 700; color: var(--ink); }
  .add-to-cart { display: inline-block; margin-top: 11px; padding: 0 4px; height: 20px; line-height: 20px; font-size: 7px; font-weight: 900; color: var(--white); background: var(--black); }

  .site-footer { position: absolute; left: 0; top: 1150px; width: 806px; height: 50px; background: var(--footer); }
  .copyright { position: absolute; left: 74px; top: 19px; font-size: 9px; color: var(--ink); }
  .social { position: absolute; left: 668px; top: 16px; display: flex; gap: 3px; }
  .social span { width: 18px; height: 18px; border-radius: 50%; border: 1px solid #5a7fb0; }
</style>
</head>
<body>
<div class="page">
  <aside class="sidebar">
    <div class="brand">
      <span class="brand-mark"></span>
      <div class="brand-name">ORV GROUP<br>ORBEL VANTRA</div>
    </div>
    <ul class="main-nav">
      <li>HOME</li>
      <li>ONLINE SHOPPING</li>
      <li>ABOUT US</li>
      <li>DESIGNER</li>
      <li>NEWS</li>
      <li>MEMBER CENTER</li>
    </ul>
  </aside>

  <section class="hero">
    <div class="hero-art" role="img" aria-label="Monochrome signature print artwork"></div>
    <div class="account-links"><span class="login">Login</span> | Register</div>
    <div class="hero-title">ORBEL VANTRA</div>
    <div class="hero-thumb thumb-1" role="img" aria-label="Look book image with colourful print beside model"></div>
    <div class="hero-thumb thumb-2" role="img" aria-label="Look book image of model with blue print"></div>
    <div class="hero-thumb thumb-3" role="img" aria-label="Look book image of model in blue print dress"></div>
    <div class="slider-dots"><span class="active"></span><span></span><span></span><span></span></div>
  </section>

  <div class="side-tools">
    <span class="active"><svg width="16" height="16" viewBox="0 0 16 16"><rect x="2" y="2" width="12" height="12" rx="2" fill="none" stroke="#fff" stroke-width="1.4"/><circle cx="8" cy="7" r="2.2" fill="#fff"/><path d="M4.5 12.5c1-2 6-2 7 0" stroke="#fff" stroke-width="1.4" fill="none"/></svg></span>
    <span><svg width="16" height="16" viewBox="0 0 16 16"><circle cx="6.5" cy="6.5" r="4" fill="none" stroke="#fff" stroke-width="1.6"/><path d="M9.5 9.5l4.5 4.5" stroke="#fff" stroke-width="2"/></svg></span>
    <span><svg width="16" height="16" viewBox="0 0 16 16"><rect x="3" y="5" width="7" height="9" fill="#fff"/><rect x="8" y="3" width="6" height="9" fill="#ddd"/></svg></span>
  </div>

  <section class="video-label"><h2>OUR VIDEO</h2></section>
  <div class="video-frame" role="img" aria-label="Fashion week video still with city skyline over water">
    <svg class="play-button" width="70" height="70" viewBox="0 0 70 70"><circle cx="35" cy="35" r="31" fill="none" stroke="#8a8a8a" stroke-width="5"/><path d="M28 22l20 13-20 13z" fill="#8a8a8a"/></svg>
  </div>

  <section class="featured">
    <h3>FEATURED PRODUCTS</h3>
    <article class="product" style="left:74px">
      <div class="product-photo photo-blue" role="img" aria-label="Model wearing blue print jumpsuit"></div>
      <p class="product-name">Black and white coat</p>
      <p class="product-price">¥ 5980.00</p>
      <p class="product-designer">Designer : Mirela Tosk</p>
      <span class="add-to-cart">ADD TO CART</span>
    </article>
    <article class="product" style="left:247px">
      <div class="product-photo photo-grey" role="img" aria-label="Model wearing print dress"></div>
      <p class="product-name">Black and white coat</p>
      <p class="product-price">¥ 5980.00</p>
      <p class="product-designer">Designer : Mirela Tosk</p>
      <span class="add-to-cart">ADD TO CART</span>
    </article>
    <article class="product" style="left:414px">
      <div class="product-photo photo-grey" role="img" aria-label="Model wearing print top and shorts"></div>
      <p class="product-name">Black and white coat</p>
      <p class="product-price">¥ 5980.00</p>
      <p class="product-designer">Designer : Mirela Tosk</p>
      <span class="add-to-cart">ADD TO CART</span>
    </article>
    <article class="product" style="left:585px">
      <div class="product-photo photo-grey" role="img" aria-label="Model wearing print crop top and white trousers"></div>
      <p class="product-name">Black and white coat</p>
      <p class="product-price">¥ 5980.00</p>
      <p class="product-designer">Designer : Mirela Tosk</p>
      <span class="add-to-cart">ADD TO CART</span>
    </article>
  </section>

  <footer class="site-footer">
    <p class="copyright">Copyright © 2014 Orbel Vantra , All rights reserved.</p>
    <div class="social"><span></span><span></span><span></span></div>
  </footer>
</div>
</body>
</html>
```